RW Framewell Inc Business cards

We need business cards using our existing logo but slightly modified. Right now the logo says RW Loadbearing Masonry. We want to keep the RW part of the design, but replace the Structural Concrete portion with "FRAMEWELL". Please see the attached file.
Ideally this would be a blank template so we can add Different Names, titles, and phone numbers later.
On the one side we want only the logo and on the other side the detail. I'm attaching an example for you to see.
Please reach out with any other questions. Our address and other details will be given out once we find a design we like.

Target Market(s)

Construction Industry

```html
<!DOCTYPE html>
<html lang="en">
<head>
<meta charset="utf-8">
<title>RW Framewell Inc – Business Cards</title>
<link href="https://fonts.googleapis.com/css2?family=Michroma&family=Open+Sans:wght@400;600&display=swap" rel="stylesheet">
<style>
  :root {
    --stage: #1d1d1f;
    --brand-blue: #1677c4;
    --brand-blue-light: #2a88d2;
    --brand-blue-dark: #0f68b0;
    --paper: #ffffff;
    --ink-grey: #6d6e71;
    --band-grey: #808184;
    --white: #ffffff;
  }
  * { box-sizing: border-box; margin: 0; padding: 0; }
  html, body {
    width: 1200px; height: 900px; overflow: hidden;
    background: var(--stage);
  }
  .canvas {
    position: relative; width: 1200px; height: 900px;
  }
  .card {
    position: absolute; left: 250px; width: 700px; height: 400px;
    overflow: hidden;
    box-shadow: 0 10px 30px rgba(0,0,0,.5);
  }
  /* Front side */
  .card--front { top: 40px; background: var(--brand-blue); }
  .card__pattern {
    position: absolute; inset: 0;
    background: linear-gradient(135deg, var(--brand-blue-light) 0%, var(--brand-blue) 50%, var(--brand-blue-dark) 100%);
  }
  .brand-name {
    position: absolute; left: 0; right: 0; top: 50%;
    transform: translateY(-50%);
    text-align: center;
    font-family: "Michroma", sans-serif;
    font-size: 40px; letter-spacing: 2px;
    color: var(--white);
  }
  /* Back side */
  .card--back { top: 470px; background: var(--paper); }
  .identity {
    position: absolute; right: 390px; top: 150px; text-align: right;
  }
  .identity__name {
    font-family: "Michroma", sans-serif;
    font-size: 27px; color: var(--brand-blue); letter-spacing: 1px;
    white-space: nowrap;
  }
  .identity__title {
    font-family: "Open Sans", sans-serif;
    font-size: 21px; color: var(--ink-grey); margin-top: 2px;
  }
  .divider {
    position: absolute; left: 332px; top: 140px; width: 2px; height: 100px;
    background: var(--brand-blue);
  }
  .contacts {
    position: absolute; left: 356px; top: 138px; list-style: none;
    font-family: "Open Sans", sans-serif; font-size: 20px; color: var(--ink-grey);
  }
  .contacts__item {
    display: flex; align-items: center; gap: 12px; height: 27px;
  }
  .contacts__icon { width: 18px; height: 18px; flex: none; }
  .address-band {
    position: absolute; left: 0; right: 0; top: 320px; height: 46px;
    background: var(--band-grey);
    font-family: "Open Sans", sans-serif; font-size: 20px; color: var(--white);
    display: flex; align-items: center; justify-content: center;
  }
</style>
</head>
<body>
<main class="canvas">
  <section class="card card--front" aria-label="Card front">
    <div class="card__pattern" role="img" aria-label="Repeating monogram pattern in light blue tones"></div>
    <p class="brand-name">RW FRAMEWELL</p>
  </section>

  <section class="card card--back" aria-label="Card back">
    <div class="identity">
      <p class="identity__name">JOHN SMITH</p>
      <p class="identity__title">Chief Officer</p>
    </div>
    <div class="divider"></div>
    <ul class="contacts">
      <li class="contacts__item">
        <svg class="contacts__icon" viewBox="0 0 24 24" aria-hidden="true"><path fill="#1677c4" d="M6.6 10.8a15.1 15.1 0 0 0 6.6 6.6l2.2-2.2a1 1 0 0 1 1-.25 11.4 11.4 0 0 0 3.6.57 1 1 0 0 1 1 1V20a1 1 0 0 1-1 1A17 17 0 0 1 3 4a1 1 0 0 1 1-1h3.5a1 1 0 0 1 1 1c0 1.25.2 2.45.57 3.57a1 1 0 0 1-.25 1z"/></svg>
        <span>+00 8 38 00 00</span>
      </li>
      <li class="contacts__item">
        <svg class="contacts__icon" viewBox="0 0 24 24" aria-hidden="true"><rect x="6" y="2" width="12" height="20" rx="2" fill="none" stroke="#1677c4" stroke-width="2"/><circle cx="12" cy="18" r="1.2" fill="#1677c4"/></svg>
        <span>+00 0 90 00 00</span>
      </li>
      <li class="contacts__item">
        <svg class="contacts__icon" viewBox="0 0 24 24" aria-hidden="true"><rect x="2" y="5" width="20" height="14" fill="#1677c4"/><path d="M2 5l10 8 10-8" fill="none" stroke="#fff" stroke-width="1.6"/></svg>
        <span>info@rwframewell.com</span>
      </li>
      <li class="contacts__item">
        <svg class="contacts__icon" viewBox="0 0 24 24" aria-hidden="true"><g fill="none" stroke="#1677c4" stroke-width="2"><circle cx="12" cy="12" r="10"/><ellipse cx="12" cy="12" rx="4.5" ry="10"/><path d="M2 12h20M4 7h16M4 17h16"/></g></svg>
        <span>www.rwframewell.com</span>
      </li>
    </ul>
    <div class="address-band">Your address line here. Country/ State</div>
  </section>
</main>
</body>
</html>
```